Storm Restoration Contractor needs a professional letterhead design

Looking for a professional letterhead design. Not looking for your cheapo MS Word standard ones that are readily available. Dont want it to be cookie cutter look like ones readily available online. We just recently changed our logo and want to freshen up all our documents. Our company handles restoring a property back to a pre-loss condition after a storm damages it. For example, wind, hail, flood, fire losses.

Target Market(s)

Property Owners, Homeowners, Property Owners, Commercial Property Owners, Property Management Companies

Industry/Entity Type

Construction Company

Requirements
Must have
• Professional, Use 1 of 2 logo options
• Storm Restoration, Roofing, Siding, Windows

```html
<!DOCTYPE html>
<html lang="en">
<head>
<meta charset="utf-8">
<title>Stonebridge Exteriors Letterhead</title>
<link rel="stylesheet" href="https://fonts.googleapis.com/css2?family=Josefin+Sans:wght@400;600&display=swap">
<style>
  :root {
    --backdrop: #ebebec;
    --paper: #ffffff;
    --brand-blue: #0a5fae;
    --brand-blue-deep: #064a8c;
    --ink: #2b2b2b;
    --watermark: #eef2f8;
  }
  * { box-sizing: border-box; margin: 0; padding: 0; }
  html, body {
    width: 1200px; height: 795px; overflow: hidden;
    background: var(--backdrop);
    font-family: "Josefin Sans", sans-serif;
  }
  .letterhead {
    position: absolute;
    left: 333px; top: 22px;
    width: 534px; height: 751px;
    background: var(--paper);
    box-shadow: 0 2px 10px rgba(0,0,0,0.08);
    overflow: hidden;
  }
  .header-swoosh { position: absolute; left: 0; top: 0; }
  .brand {
    position: absolute; left: 30px; top: 48px;
    display: flex; flex-direction: column; align-items: flex-start; gap: 6px;
  }
  .brand-mark {
    width: 40px; height: 40px; border-radius: 50%;
    border: 3px solid var(--brand-blue);
  }
  .brand-name {
    color: var(--brand-blue);
    font-weight: 600; font-size: 11px; letter-spacing: 1.2px;
    text-transform: uppercase;
  }
  .watermark {
    position: absolute; left: 172px; top: 210px;
    width: 200px; height: 200px; border-radius: 50%;
    border: 14px solid var(--watermark);
  }
  .footer {
    position: absolute; left: 34px; bottom: 30px;
    font-size: 10.5px; line-height: 1.45; color: var(--ink);
  }
  .footer-name, .footer-web { color: var(--brand-blue); }
  .contact-row { display: flex; align-items: center; gap: 4px; }
  .contact-icon {
    width: 10px; height: 10px; border-radius: 50%;
    background: var(--brand-blue-deep);
    display: inline-flex; align-items: center; justify-content: center;
  }
</style>
</head>
<body>
  <main class="letterhead">
    <svg class="header-swoosh" width="534" height="260" viewBox="0 0 534 260" aria-hidden="true">
      <path d="M300 0 L400 0 C330 30 300 120 210 190 C150 235 70 250 0 252 L0 238 C80 232 150 205 205 150 C255 100 260 40 300 0 Z" fill="var(--brand-blue)"/>
      <path d="M330 0 L400 0 C340 25 315 90 270 140 C300 80 310 30 330 0 Z" fill="var(--brand-blue-deep)"/>
    </svg>

    <div class="brand">
      <span class="brand-mark"></span>
      <span class="brand-name">Stonebridge Exteriors</span>
    </div>

    <div class="watermark" aria-hidden="true"></div>

    <footer class="footer">
      <div class="footer-name">Stonebridge Exteriors</div>
      <div>2250 Harbor Lane, Fairview, CA 90210</div>
      <div class="contact-row">
        <span class="contact-icon">
          <svg width="6" height="6" viewBox="0 0 10 10"><path d="M2 1 L4 1 L5 3 L4 4 Q5 6 6 6 L7 5 L9 6 L9 8 Q9 9 8 9 Q1 9 1 2 Q1 1 2 1Z" fill="#fff"/></svg>
        </span>(555) 214-7730
        <span class="contact-icon">
          <svg width="6" height="6" viewBox="0 0 10 10"><path d="M2 1 L4 1 L5 3 L4 4 Q5 6 6 6 L7 5 L9 6 L9 8 Q9 9 8 9 Q1 9 1 2 Q1 1 2 1Z" fill="#fff"/></svg>
        </span>(555) 214-7731
        <span class="contact-icon">
          <svg width="6" height="6" viewBox="0 0 10 10"><rect x="1" y="2" width="8" height="6" fill="#fff"/><path d="M1 2 L5 5 L9 2" stroke="var(--brand-blue-deep)" fill="none"/></svg>
        </span>info@stonebridgeexteriors.com
      </div>
      <div class="footer-web">www.stonebridgeexteriors.com</div>
    </footer>
  </main>
</body>
</html>
```